I need a business card design for a new business based in South West Australia.
I specialize in residential window cleaning & general handyman maintenance.

Dale Marsh - 412 SILVER HAWK DETAILING
- Window Cleaning
- House Maintenance

```html
<!DOCTYPE html>
<html lang="en">
<head>
<meta charset="utf-8">
<title>Silver Hawk Detailing – Business Card</title>
<link href="https://fonts.googleapis.com/css2?family=Source+Sans+3:wght@400;600&display=swap" rel="stylesheet">
<style>
  :root {
    --backdrop: #141414;
    --card: #ffffff;
    --accent: #ec6408;
    --ink: #3a3a3a;
  }
  * { margin: 0; padding: 0; box-sizing: border-box; }
  html, body {
    width: 1200px; height: 900px; overflow: hidden;
    background: var(--backdrop);
  }
  .stage { position: relative; width: 1200px; height: 900px; }
  .card {
    position: absolute; top: 170px; width: 347px; height: 561px;
    background: var(--card);
    font-family: "Source Sans 3", "Myriad Pro", sans-serif;
    color: var(--ink); text-align: center;
  }
  .card--front { left: 259px; }
  .card--back { left: 631px; }
  .band {
    position: absolute; left: 102px; width: 143px; height: 30px;
    background: var(--accent);
  }
  .band--top { top: 0; }
  .band--bottom { bottom: 0; }
  .brand-name {
    font-family: "Source Sans 3", "Myriad Pro", sans-serif;
    font-weight: 600; color: var(--accent);
  }
  .front-brand {
    position: absolute; top: 98px; left: 0; right: 0;
    font-size: 28px; line-height: 1.15;
  }
  .holder { position: absolute; top: 276px; left: 0; right: 0; }
  .holder__name {
    font-weight: 600; font-size: 23px; color: var(--accent);
    text-transform: uppercase; letter-spacing: 0.2px; line-height: 1.2;
  }
  .holder__role { font-size: 15px; margin-top: 1px; }
  .contact { position: absolute; top: 347px; left: 0; right: 0; font-size: 15px; line-height: 21px; }
  .contact__row { display: flex; justify-content: center; align-items: center; gap: 9px; }
  .contact__icon { width: 11px; height: 11px; fill: var(--accent); }
  .address { position: absolute; top: 465px; left: 0; right: 0; font-size: 15px; line-height: 17px; }
  .back-lockup { position: absolute; top: 298px; left: 0; right: 0; }
  .back-lockup .brand-name { font-size: 30px; line-height: 1.1; }
  .tagline { margin-top: 4px; font-size: 13px; color: var(--ink); }
</style>
</head>
<body>
<main class="stage">
  <section class="card card--front">
    <div class="band band--top"></div>
    <p class="brand-name front-brand">Silver Hawk<br>Detailing</p>
    <div class="holder">
      <p class="holder__name">Dale Marsh</p>
      <p class="holder__role">Managing Director</p>
    </div>
    <div class="contact">
      <p class="contact__row">
        <svg class="contact__icon" viewBox="0 0 12 12" aria-hidden="true"><path d="M1 4c0-2 2-3 5-3s5 1 5 3l-2 1-1-1.5H4L3 5zM3 6h6l1 5H2z"/></svg>
        <span>412-555-0187</span>
      </p>
      <p class="contact__row">
        <svg class="contact__icon" viewBox="0 0 12 12" aria-hidden="true"><path d="M1 3h10v7H1zM1.5 3.5 6 7l4.5-3.5" stroke="#fff" stroke-width="1"/></svg>
        <span>hello@silverhawk.au</span>
      </p>
    </div>
    <div class="address">
      <p>412 Hawk Ridge Road</p>
      <p>Busselton WA 6280</p>
    </div>
    <div class="band band--bottom"></div>
  </section>

  <section class="card card--back">
    <div class="back-lockup">
      <p class="brand-name">Silver Hawk Detailing</p>
      <p class="tagline">Window cleaning &amp; house maintenance</p>
    </div>
  </section>
</main>
</body>
</html>
```